Verpackungen für Parfum-Proben
Besten Dank! Das Team ist begeistert - also bin ich es auch und wir freuen uns schon, unsere Parfum Proben in Zukunft in diesem tollen Design weitergeben zu können! Danke!
Zielgruppe
Hallo allerseits! Wir sind im Direktvertrieb in den Bereichen Parfum & Kosmetik tätig.
Aufgabenstellung
Für unsere Parfum-Proben benötige ich ein ansprechendes, modernes Design.
Das Design muss relativ neutral gehalten werden, da die Blister sowohl für Herren- als auch Damenproben verwendet werden.
Auf Vorder- und Rückseite soll unser Team-Logo (NaseNomade®) sichtbar sein (Vorderseite größer, Rückseite kleiner).
Auf der linken Innenseite sollte Plätz für einen netten Spruch (den ich mir noch überlege) sein.
Auf der Rückseite muss Platz (weißes / helles Feld) für einen Stempel und/oder Aufkleber (Kontaktdaten des Distributors) sein.
Unser Logo ist Lila - Das farbliche Design sollte dazu passen.
Bei Fragen, einfach Nachricht :)
Daten:
Endformat: 133 x 74 mm
Datenformat: 139 x 80 mm
1-teilig, gestanzt, genutet, einseitig geklebt geliefert
Bitte verwenden Sie für positive Schriftstärken mindestens 9pt (ca. 3,17mm) und bei negativen Schriftstärken mindestens 13pt (ca. 4,59mm).
Abmessungen / Druck- / Designvorlage, Logo, etc.: https://dateiwolke-beispiel.de/ordner/X7pLrT2k#v9wQe4nZb6Hs1Ym_d8cKfa

```html
<!DOCTYPE html>
<html lang="de">
<head>
<meta charset="utf-8">
<title>NaseNomade – Probenblister, flach</title>
<link href="https://fonts.googleapis.com/css2?family=Pathway+Gothic+One&display=swap" rel="stylesheet">
<style>
  :root {
    --canvas-bg: #e2e2e2;
    --violet: #6a55a3;
    --violet-light: #8c7bc0;
    --violet-pale: #9d8ecb;
    --quote-ink: #dcd5f0;
    --white: #ffffff;
    --die-line: #e0147a;
    --skin: #f0c9a0;
    --hair: #f2b3cf;
  }
  html, body {
    margin: 0;
    padding: 0;
    width: 1200px;
    height: 2330px;
    overflow: hidden;
    background: var(--canvas-bg);
    font-family: "Pathway Gothic One", "Arial Narrow", sans-serif;
  }
  .sheet {
    position: absolute;
    left: 80px;
    width: 1040px;
    height: 573px;
    background: var(--violet);
    overflow: hidden;
  }
  .sheet--outside { top: 542px; }
  .sheet--inside { top: 1215px; }

  .halftone-field {
    position: absolute;
    top: 0;
    bottom: 0;
  }
  .sheet--outside .halftone-field {
    left: 40%;
    right: 0;
    background: radial-gradient(ellipse at 75% 35%, var(--violet-pale) 0%, var(--violet-light) 40%, var(--violet) 85%);
  }
  .sheet--inside .halftone-field {
    left: 0;
    width: 58%;
    background: radial-gradient(ellipse at 35% 40%, var(--violet-light) 0%, var(--violet) 80%);
  }

  .illustration {
    position: absolute;
    left: 61%;
    right: 2%;
    top: 0;
    bottom: 0;
    background: linear-gradient(180deg, var(--hair) 0%, var(--hair) 18%, var(--skin) 30%, var(--skin) 80%, var(--violet) 100%);
    border-radius: 45% 45% 6% 6% / 30% 30% 4% 4%;
    opacity: 0.9;
  }

  .team-name {
    position: absolute;
    display: flex;
    align-items: center;
    gap: 12px;
    color: var(--white);
    font-size: 40px;
    letter-spacing: 1px;
    white-space: nowrap;
  }
  .team-name__dot {
    width: 22px;
    height: 22px;
    border-radius: 50%;
    background: var(--white);
  }
  .sheet--outside .team-name { left: 10%; top: 24%; }
  .sheet--inside .team-name { left: 71%; top: 40%; }

  .stamp-field {
    position: absolute;
    left: 5.5%;
    top: 72%;
    width: 34.5%;
    height: 23.5%;
    background: var(--white);
    border-radius: 14px;
  }

  .quote {
    position: absolute;
    left: 2%;
    width: 44%;
    top: 23%;
    margin: 0;
    text-align: center;
    color: var(--quote-ink);
    font-size: 44px;
    line-height: 1.35;
    text-transform: uppercase;
  }
  .quote__author {
    display: block;
    font-size: 36px;
  }

  .die-lines {
    position: absolute;
    inset: 0;
    width: 100%;
    height: 100%;
    pointer-events: none;
  }
</style>
</head>
<body>

<section class="sheet sheet--outside" aria-label="Außenseite">
  <div class="halftone-field"></div>
  <div class="illustration" role="img" aria-label="Pop-Art-Illustration einer Frau mit rosa Haarknoten, Brille und Parfumprobe, die eine Kusshand wirft"></div>
  <div class="team-name"><span class="team-name__dot"></span>NaseNomade</div>
  <div class="stamp-field" aria-label="Feld für Stempel oder Aufkleber"></div>
  <svg class="die-lines" viewBox="0 0 1040 573" preserveAspectRatio="none" aria-hidden="true">
    <g fill="none" stroke="var(--die-line)" stroke-width="2">
      <line x1="473" y1="0" x2="473" y2="573"/>
      <line x1="573" y1="0" x2="573" y2="573"/>
      <rect x="413" y="95" width="110" height="55"/>
      <rect x="373" y="255" width="200" height="75"/>
      <rect x="413" y="440" width="110" height="55"/>
    </g>
  </svg>
</section>

<section class="sheet sheet--inside" aria-label="Innenseite">
  <div class="halftone-field"></div>
  <p class="quote">Ein&nbsp; Parfüm ist immer<br>auch ein Statement<br>über das, was du bist.<span class="quote__author">Lena Hartwig</span></p>
  <div class="team-name"><span class="team-name__dot"></span>NaseNomade</div>
  <svg class="die-lines" viewBox="0 0 1040 573" preserveAspectRatio="none" aria-hidden="true">
    <g fill="none" stroke="var(--die-line)" stroke-width="2">
      <line x1="470" y1="0" x2="470" y2="573"/>
      <line x1="572" y1="0" x2="572" y2="573"/>
      <rect x="520" y="95" width="110" height="55"/>
      <rect x="470" y="255" width="200" height="75"/>
      <rect x="520" y="440" width="110" height="55"/>
    </g>
  </svg>
</section>

</body>
</html>
```